KLV Plant Services

We are a heavy diesel mechanical business with additional air con certificates, remapping engine rebuilt

Contact Information for Business Card

Company Name, Director Name, Managing Director, Contact details, email and website

Font styles to use
Serif
Script

```html
<!DOCTYPE html>
<html lang="en">
<head>
<meta charset="utf-8">
<title>KLV Plant Services – Business Card</title>
<link rel="stylesheet" href="https://fonts.googleapis.com/css2?family=Montserrat:wght@700&family=Questrial&display=swap">
<style>
  :root {
    --page-bg: #d9d9d9;
    --card-dark: #0c0c0c;
    --card-dark-glow: #2a2a2a;
    --card-light: #ffffff;
    --card-light-shade: #ececec;
    --navy: #2a2878;
    --navy-bright: #4a46b8;
    --ink: #2c2c34;
    --muted: #5a5a62;
    --rule: #8a8a90;
  }
  * { box-sizing: border-box; margin: 0; padding: 0; }
  html, body {
    width: 1200px; height: 900px; overflow: hidden;
    background: var(--page-bg);
  }
  .sheet {
    width: 1200px; height: 900px;
    display: flex; flex-direction: column;
    align-items: center; justify-content: center; gap: 40px;
  }
  .card {
    width: 700px; height: 400px;
    border-radius: 36px;
    position: relative;
    box-shadow: 0 10px 24px rgba(0,0,0,0.25);
  }
  .card--front {
    background: radial-gradient(ellipse at 50% 45%, var(--card-dark-glow) 0%, var(--card-dark) 65%);
    display: flex; align-items: center; justify-content: center;
  }
  .card--back {
    background: linear-gradient(160deg, var(--card-light-shade) 0%, var(--card-light) 45%);
  }
  .brand {
    display: flex; align-items: center; gap: 14px;
    font-family: "Montserrat", sans-serif; font-weight: 700;
  }
  .brand__mark {
    width: 34px; height: 34px; border-radius: 50%;
  }
  .brand__name { font-size: 34px; letter-spacing: 0.5px; }
  .card--front .brand__name { color: var(--navy-bright); }
  .card--front .brand__mark { background: var(--navy-bright); }
  .card--back .brand {
    position: absolute; left: 44px; top: 64px;
  }
  .card--back .brand__name { color: var(--navy); font-size: 30px; }
  .card--back .brand__mark { background: var(--navy); width: 30px; height: 30px; }

  .person {
    position: absolute; right: 410px; bottom: 70px;
    text-align: right;
  }
  .person__name {
    font-family: "Montserrat", sans-serif; font-weight: 700;
    color: var(--navy); font-size: 19px; letter-spacing: 0.5px;
  }
  .person__role {
    font-family: "Questrial", sans-serif;
    color: var(--muted); font-size: 15px; margin-top: 4px;
  }
  .divider {
    position: absolute; left: 308px; bottom: 56px;
    width: 1px; height: 130px; background: var(--rule);
  }
  .contacts {
    position: absolute; left: 326px; bottom: 58px;
    list-style: none;
    font-family: "Questrial", sans-serif; color: var(--ink); font-size: 15px;
  }
  .contacts li { display: flex; align-items: flex-start; gap: 9px; line-height: 1.35; margin-top: 5px; }
  .contacts svg { width: 15px; height: 15px; flex: none; margin-top: 2px; fill: var(--navy); }
</style>
</head>
<body>
<main class="sheet">
  <section class="card card--front" aria-label="Card front">
    <div class="brand">
      <span class="brand__mark"></span>
      <span class="brand__name">KLV Plant Services</span>
    </div>
  </section>

  <section class="card card--back" aria-label="Card back">
    <div class="brand">
      <span class="brand__mark"></span>
      <span class="brand__name">KLV Plant Services</span>
    </div>

    <div class="person">
      <p class="person__name">LIAM NORRIS</p>
      <p class="person__role">Managing Director</p>
    </div>

    <span class="divider"></span>

    <ul class="contacts">
      <li>
        <svg viewBox="0 0 24 24" aria-hidden="true"><path d="M6.6 10.8a15 15 0 0 0 6.6 6.6l2.2-2.2a1 1 0 0 1 1-.25 11.4 11.4 0 0 0 3.6.57 1 1 0 0 1 1 1V20a1 1 0 0 1-1 1A17 17 0 0 1 3 4a1 1 0 0 1 1-1h3.5a1 1 0 0 1 1 1c0 1.25.2 2.45.57 3.57a1 1 0 0 1-.25 1z"/></svg>
        <span>0400 123 456</span>
      </li>
      <li>
        <svg viewBox="0 0 24 24" aria-hidden="true"><path d="M2 5h20v14H2z M2 5l10 8 10-8" /><path d="M3 6.2l9 7.2 9-7.2V18H3z" fill="#fff" opacity="0.25"/></svg>
        <span>admin@klvplantservices.net</span>
      </li>
      <li>
        <svg viewBox="0 0 24 24" aria-hidden="true"><path d="M12 2a10 10 0 1 0 0 20 10 10 0 0 0 0-20zm0 2c.9 0 2.2 1.9 2.7 5H9.3C9.8 5.9 11.1 4 12 4zM4.3 11h3c0 .7 0 1.4.1 2h-3a8 8 0 0 1-.1-2zm.5 4h2.9c.4 1.6 1 2.9 1.7 3.8A8 8 0 0 1 4.8 15zm2.6-6H4.8a8 8 0 0 1 3.8-3.8C8.1 6.1 7.6 7.5 7.4 9zM12 20c-.9 0-2.2-1.9-2.7-5h5.4c-.5 3.1-1.8 5-2.7 5zm2.9-7H9.1a16 16 0 0 1 0-2h5.8a16 16 0 0 1 0 2zm.5 5.8c.7-.9 1.3-2.2 1.7-3.8h2.9a8 8 0 0 1-4.6 3.8zM16.7 13c.1-.6.1-1.3.1-2h3a8 8 0 0 1 0 2zm-.1-4c-.2-1.5-.7-2.9-1.2-3.8A8 8 0 0 1 19.2 9z"/></svg>
        <span>www.klvplantservices.net</span>
      </li>
      <li>
        <svg viewBox="0 0 24 24" aria-hidden="true"><path d="M12 2a7 7 0 0 0-7 7c0 5.2 7 13 7 13s7-7.8 7-13a7 7 0 0 0-7-7zm0 9.5A2.5 2.5 0 1 1 12 6.5a2.5 2.5 0 0 1 0 5z"/></svg>
        <span>48 Sample Road, Greenvale<br>WA 6000, Australia</span>
      </li>
    </ul>
  </section>
</main>
</body>
</html>
```